Real Estate Company
Residential & Commercial
Sales & Property Management

would like to use the logo i uploaded but would really love a black back ground...I think with the gold fleur dis lis and the maroon lettering it would really look great!

Industry/Entity Type

Business

Contact Information for Business Card

Our Coastal Real Estate Co.
Danielle Forbis
Broker/Owner
337-284-6093 Cell
337-726-0348 Office
8142 Willet Rd Cypress Hollow LA 70999

```html
<!DOCTYPE html>
<html lang="en">
<head>
<meta charset="utf-8">
<title>Our Coastal Real Estate Co. – Business Card</title>
<link rel="stylesheet" href="https://fonts.googleapis.com/css2?family=Cinzel:wght@400;600&display=swap">
<style>
  :root {
    --stage: #161616;
    --card-black: #0b0b0b;
    --card-white: #fbfbfa;
    --gold: #c9a449;
    --gold-light: #e6cf86;
    --maroon: #7b1d24;
    --ink: #2b2b2b;
    --tan: #cfae7a;
  }
  * { box-sizing: border-box; margin: 0; padding: 0; }
  html, body { width: 1200px; height: 871px; overflow: hidden; }
  body {
    background: var(--stage);
    font-family: "Cinzel", Georgia, serif;
    position: relative;
  }
  .card {
    position: absolute;
    width: 560px;
    height: 320px;
    box-shadow: 0 18px 40px rgba(0,0,0,.6);
  }

  /* Front */
  .card-front {
    left: 80px; top: 90px;
    background: var(--card-black);
    border: 14px solid var(--gold);
    display: flex; align-items: center; justify-content: center;
  }
  .card-front::before {
    content: "";
    position: absolute; inset: 0;
    border: 1px solid var(--gold-light);
    opacity: .35;
  }
  .brand {
    display: flex; align-items: center; gap: 14px;
  }
  .brand-mark {
    width: 26px; height: 26px; border-radius: 50%;
    background: var(--gold);
    flex: none;
  }
  .brand-name {
    font-weight: 600;
    font-size: 30px;
    line-height: 1.15;
    letter-spacing: .5px;
    color: var(--tan);
  }
  .card-front .brand-name { max-width: 360px; }

  /* Back */
  .card-back {
    left: 560px; top: 470px;
    background: var(--card-white);
    display: grid;
    grid-template-columns: 1fr 1fr;
    align-items: center;
    padding: 0 36px 0 34px;
  }
  .card-back .brand-name {
    color: var(--maroon);
    font-size: 22px;
    max-width: 200px;
    border-bottom: 1px solid var(--maroon);
    padding-bottom: 4px;
  }
  .card-back .brand-mark { width: 20px; height: 20px; }

  .contact { color: var(--ink); font-size: 12.5px; letter-spacing: .4px; }
  .contact-name {
    color: var(--maroon); font-size: 17px; font-weight: 600; letter-spacing: 1.5px;
  }
  .contact-role { font-size: 11.5px; margin-bottom: 22px; }
  .contact-address { line-height: 1.45; margin-bottom: 14px; }
  .contact-line { display: flex; align-items: center; gap: 10px; line-height: 1.7; }
  .contact-line svg { width: 12px; height: 12px; flex: none; }
</style>
</head>
<body>

  <section class="card card-front" aria-label="Card front">
    <div class="brand">
      <span class="brand-mark"></span>
      <span class="brand-name">Our Coastal Real Estate Co.</span>
    </div>
  </section>

  <section class="card card-back" aria-label="Card back">
    <div class="brand">
      <span class="brand-mark"></span>
      <span class="brand-name">Our Coastal Real Estate Co.</span>
    </div>

    <div class="contact">
      <p class="contact-name">Danielle Forbis</p>
      <p class="contact-role">Broker/Owner</p>
      <p class="contact-address">Office 8142 Willet Rd<br>Cypress Hollow LA 70999</p>
      <p class="contact-line">
        <svg viewBox="0 0 12 12" aria-hidden="true"><path d="M1 4.5 Q6 1 11 4.5 L10 6 L8 5 L8 4 Q6 3.3 4 4 L4 5 L2 6 Z M3 7 H9 L10 11 H2 Z" fill="var(--gold)"/></svg>
        337-284-6093
      </p>
      <p class="contact-line">
        <svg viewBox="0 0 12 12" aria-hidden="true"><rect x="3" y="0.5" width="6" height="11" rx="1.2" fill="none" stroke="var(--gold)" stroke-width="1.2"/><rect x="4.3" y="2" width="3.4" height="6" fill="var(--gold)"/></svg>
        Cell 337-726-0348
      </p>
    </div>
  </section>

</body>
</html>
```